Human Resource Consulting practice needs a business card design

We need a business card design (double sided colour) for our Human Resource (HR) consulting practice in regional New South Wales, australia. Our business name is Staff Compass. We support small and medium business across the Mid North Coast of New South Wales by providing them with outsourced HR support, services and products to help them achieve compliance with workplace legislation and across all areas of the employment lifecycle from recruitment to termination and everything in between. Our corporate colours are hot pink and black. The final design should communicate professionalism, trust, people focus.
I have attached the current (old) business card for your reference.

Target Market(s)

Business owners and high level managers

Industry/Entity Type

Business

Contact Information for Business Card

Name
Title
Phone no
Mobile no
Address
PO Box
email address
website

Colors
e34197

Requirements
Must have
• Tempate for changing business card personal details including Name, position title, mobile number, email address.
• Keep current logo and colours as per attached
• Logo must be presented in 2 colours or black only not white
Nice to have
• One side logo and graphic only other side logo and personal details
Should not have
• Should not be the same as the current version (attached) but a modern interpretation.
• Does not need a busy reverse side with our list of services as per current version. I feel this is too busy.
• No photos

```html
<!DOCTYPE html>
<html lang="en">
<head>
<meta charset="utf-8">
<title>Staff Compass – Business Card</title>
<link rel="stylesheet" href="https://fonts.googleapis.com/css2?family=Archivo+Black&family=Michroma&display=swap">
<style>
  :root {
    --hot-pink: #ec0a94;
    --ink: #1c1c1c;
    --paper: #ffffff;
    --stage: #2b2b2b;
    --rule: rgba(40, 20, 30, 0.55);
  }
  * { box-sizing: border-box; margin: 0; padding: 0; }
  html, body {
    width: 1200px;
    height: 1189px;
    overflow: hidden;
    background: var(--stage);
  }
  .stage {
    width: 1200px;
    height: 1189px;
    display: flex;
    flex-direction: column;
    align-items: center;
    justify-content: center;
    gap: 34px;
  }
  .card {
    position: relative;
    width: 900px;
    height: 550px;
    background: var(--hot-pink);
    border-radius: 30px;
    color: var(--ink);
    font-family: "Michroma", sans-serif;
    overflow: hidden;
  }

  /* Front side */
  .card--front .brand {
    position: absolute;
    left: 0; right: 0;
    top: 190px;
    text-align: center;
    font-size: 66px;
    letter-spacing: 1px;
    white-space: nowrap;
  }
  .brand__dot {
    display: inline-block;
    width: 22px; height: 22px;
    border-radius: 50%;
    background: var(--ink);
    margin-right: 18px;
    vertical-align: middle;
  }
  .card--front .web-line {
    position: absolute;
    left: 0; right: 0;
    top: 350px;
    display: flex;
    align-items: center;
    justify-content: center;
    gap: 22px;
    font-size: 20px;
    letter-spacing: 2px;
  }
  .web-line .rule {
    width: 110px;
    height: 1px;
    background: var(--rule);
  }

  /* Back side */
  .card--back .brand {
    position: absolute;
    left: 60px;
    top: 95px;
    font-size: 54px;
    letter-spacing: 1px;
    white-space: nowrap;
  }
  .card--back .brand .brand__dot { width: 18px; height: 18px; margin-right: 14px; }
  .person {
    position: absolute;
    right: 60px;
    top: 190px;
    text-align: right;
  }
  .person__name {
    font-family: "Archivo Black", sans-serif;
    color: var(--paper);
    font-size: 34px;
    letter-spacing: 1px;
  }
  .person__title {
    font-size: 15px;
    letter-spacing: 1.5px;
    margin-top: 4px;
  }
  .card--back .divider {
    position: absolute;
    left: 60px;
    right: 60px;
    top: 280px;
    height: 1px;
    background: var(--rule);
  }
  .contacts {
    position: absolute;
    left: 60px;
    top: 318px;
    list-style: none;
  }
  .contacts li {
    display: flex;
    align-items: center;
    gap: 18px;
    height: 44px;
    font-size: 19px;
    letter-spacing: 1px;
    white-space: nowrap;
  }
  .icon {
    width: 32px;
    height: 32px;
    flex: none;
  }
  .address {
    position: absolute;
    right: 60px;
    top: 312px;
    text-align: right;
    font-size: 18px;
    font-style: normal;
    line-height: 1.6;
    letter-spacing: 1px;
    white-space: nowrap;
  }
</style>
</head>
<body>
<main class="stage">

  <section class="card card--front" aria-label="Card front">
    <div class="brand"><span class="brand__dot"></span>Staff Compass</div>
    <div class="web-line">
      <span class="rule"></span>
      <span>www.staffcompass.com.au</span>
      <span class="rule"></span>
    </div>
  </section>

  <section class="card card--back" aria-label="Card back">
    <div class="brand"><span class="brand__dot"></span>Staff Compass</div>

    <div class="person">
      <div class="person__name">Clara Benton</div>
      <div class="person__title">PRINCIPAL CONSULTANT</div>
    </div>

    <div class="divider"></div>

    <ul class="contacts">
      <li>
        <svg class="icon" viewBox="0 0 32 32" aria-hidden="true">
          <rect width="32" height="32" rx="6" fill="#fff"/>
          <path d="M8 12c0-3 4-4 8-4s8 1 8 4l-3 1-1-2h-8l-1 2z" fill="#ec0a94"/>
          <rect x="9" y="15" width="14" height="9" rx="2" fill="#ec0a94"/>
          <circle cx="16" cy="19.5" r="2.5" fill="#fff"/>
        </svg>
        <span>02 5550 1482</span>
      </li>
      <li>
        <svg class="icon" viewBox="0 0 32 32" aria-hidden="true">
          <rect width="32" height="32" rx="6" fill="#fff"/>
          <rect x="10" y="5" width="12" height="22" rx="2" fill="#ec0a94"/>
          <rect x="12" y="8" width="8" height="9" fill="#fff"/>
          <circle cx="16" cy="22" r="1.6" fill="#fff"/>
        </svg>
        <span>0400 555 018</span>
      </li>
      <li>
        <svg class="icon" viewBox="0 0 32 32" aria-hidden="true">
          <rect width="32" height="32" rx="6" fill="#fff"/>
          <rect x="6" y="9" width="20" height="14" fill="none" stroke="#ec0a94" stroke-width="2"/>
          <path d="M6 9l10 8 10-8" fill="none" stroke="#ec0a94" stroke-width="2"/>
        </svg>
        <span>clara@staffcompass.com.au</span>
      </li>
      <li>
        <svg class="icon" viewBox="0 0 32 32" aria-hidden="true">
          <rect width="32" height="32" rx="6" fill="#fff"/>
          <circle cx="16" cy="16" r="10" fill="none" stroke="#ec0a94" stroke-width="2"/>
          <ellipse cx="16" cy="16" rx="4.5" ry="10" fill="none" stroke="#ec0a94" stroke-width="1.5"/>
          <path d="M6 16h20M8 11h16M8 21h16" stroke="#ec0a94" stroke-width="1.5"/>
        </svg>
        <span>www.staffcompass.com.au</span>
      </li>
    </ul>

    <address class="address">
      P.O. Box 120<br>
      Harbour Bay, NSW 2400
    </address>
  </section>

</main>
</body>
</html>
```